Agriculture farming Hemp and CBD

The logo is in works with your company now, should be ready in a few days. We have our Domain (kestrelbrookhollow.com) We would like to see incorporated seed to growth, but not necessary. we would like to nature colors and some black and green. we have our farm and will be growing and selling HEMP and CBD we are based in the state of Virginia. Would like to incorporate the words pause, play, rewind if possible but not necessary.

Target Market(s)

20 years old to elderly

Coding

Coded - Design and coding required

Number of Pages Required

3 page

Font styles to use
Serif

Requirements
Must have
• I'm not sure on the must haves, we are open to any ideas, we would definitely like to see Hemp and CBD included, may the life cycle of seed to plant. We must have a pop up asking if you are 20 years old before they can enter our site and to view or purchase our product. I want the design to be totally different than what i uploaded.
Nice to have
• Would like to see natural colors as well as black and green
Should not have
• I want

```html
<!DOCTYPE html>
<html lang="en">
<head>
<meta charset="utf-8">
<title>Kestrel Brook Hollow – Home and Age Verification</title>
<link rel="stylesheet" href="https://fonts.googleapis.com/css2?family=Lato:ital,wght@0,400;0,700;0,900;1,400&display=swap">
<style>
:root{
  --backdrop:#a3d9a5;
  --green:#25b012;
  --orange:#f2691e;
  --black:#000;
  --ink:#222;
  --text:#444;
  --soft:#f1f1f1;
  --white:#fff;
  --footer:#1f1f17;
}
*{box-sizing:border-box;margin:0;padding:0}
html,body{width:907px;height:1200px;overflow:hidden}
body{background:var(--backdrop);font-family:'Lato',sans-serif;position:relative}
.screen{position:absolute;top:11px;width:756px;height:2170px;transform:scale(.5425);transform-origin:0 0;overflow:hidden;background:var(--white)}
.screen--home{left:22px}
.screen--gate{left:465px}
.abs{position:absolute}
.topbar{top:0;left:0;width:756px;height:33px;background:var(--white)}
.social{display:flex;gap:10px;align-items:center}
.social span{width:10px;height:10px;border-radius:50%;background:#333;display:block}
.topbar .social{position:absolute;left:48px;top:12px}
.call{position:absolute;right:46px;top:10px;font-size:12px;font-weight:700;color:var(--ink);display:flex;align-items:center;gap:6px}
.call b{color:var(--green)}
.navbar{top:33px;left:0;width:756px;height:65px;background:var(--black)}
.brand{position:absolute;left:52px;top:18px;color:var(--white);font-size:21px;font-weight:900;letter-spacing:-.3px}
.menu{position:absolute;left:318px;top:29px;display:flex;gap:27px;font-size:8.5px;color:var(--white);font-weight:700}
.menu .active{color:var(--green)}
.hero{top:98px;left:0;width:756px;height:402px;background:radial-gradient(ellipse at 60% 40%,#6b6a3a 0%,#3c4a26 35%,#22301a 70%,#1a1c14 100%)}
.hero h1{position:absolute;top:130px;width:100%;text-align:center;color:var(--white);font-size:45px;font-weight:900;letter-spacing:.5px}
.hero p{position:absolute;top:188px;left:178px;width:400px;text-align:center;color:var(--white);font-size:14px;font-weight:700;line-height:19px}
.btn{display:inline-block;border-radius:14px;color:var(--white);font-size:9px;font-weight:700;text-align:center;line-height:25px;height:25px;width:104px}
.btn--green{background:var(--green)}
.btn--orange{background:var(--orange)}
.hero .btn{position:absolute;top:240px;left:322px;width:114px}
.dots{position:absolute;top:371px;left:357px;display:flex;gap:7px}
.dots span{width:5px;height:5px;border-radius:50%;background:var(--white)}
.dots span:first-child{background:var(--green)}
h2.title{font-size:21px;font-weight:900;color:var(--black);text-align:center;width:756px;position:absolute;left:0}
.welcome-text{top:570px;left:50px;width:656px;text-align:center;font-size:9.5px;line-height:16px;color:var(--text)}
.panel{background:var(--soft)}
.panel h3{font-size:20px;font-weight:900;color:var(--green);margin-bottom:9px}
.panel p{font-size:9.5px;line-height:16.3px;color:var(--text);width:312px;margin-bottom:19px}
.photo{position:absolute}
.blog{position:absolute;top:1341px;width:210px}
.blog .thumb{height:133px}
.blog h4{margin-top:18px;font-size:11.5px;font-weight:900;color:var(--green)}
.blog p{margin-top:6px;font-size:9.5px;line-height:16px;color:var(--text);width:212px}
.blog .btn{margin-top:14px}
.reviews h3{position:absolute;top:1694px;left:48px;font-size:16px;font-weight:700;color:var(--black)}
.arrows{position:absolute;top:1694px;left:322px;font-size:17px;color:#333;letter-spacing:6px}
.quote-mark{position:absolute;top:1730px;left:48px;font-family:Georgia,serif;font-size:52px;font-weight:900;color:var(--orange);line-height:1}
.review-text{position:absolute;top:1764px;left:48px;width:305px;font-size:9px;line-height:17.5px;font-style:italic;color:var(--text)}
.reviewer{position:absolute;top:1864px;left:48px;font-size:9px;font-weight:700;color:var(--green)}
.footer{top:1925px;left:0;width:756px;height:245px;background:linear-gradient(180deg,#2b2b22 0%,#1e1e16 60%,#141411 100%)}
.fcol{position:absolute;top:70px;font-size:8.5px;color:#ddd;line-height:21px}
.fcol h5{font-size:10px;font-weight:700;color:var(--orange);margin-bottom:2px;line-height:14px}
.fcol .pair{display:grid;grid-template-columns:63px 80px}
.contact-row{display:flex;gap:10px}
.contact-row i{width:8px;font-style:normal;color:#ddd}
.fdivider{position:absolute;top:190px;left:47px;width:662px;height:1px;background:rgba(255,255,255,.15)}
.copyright{position:absolute;top:214px;left:47px;font-size:7.5px;color:#ddd}
.footer .social{position:absolute;top:210px;left:538px;gap:15px}
.footer .social span{width:12px;height:12px;background:#eee}
.overlay{position:absolute;inset:0;background:rgba(45,45,45,.42)}
.age-modal{position:absolute;left:245px;top:164px;width:267px;height:207px;background:rgba(255,255,255,.9);border-radius:6px;text-align:center}
.age-modal .close{position:absolute;right:10px;top:6px;font-size:13px;font-weight:900;color:var(--black)}
.age-modal h3{margin-top:53px;font-size:15px;font-weight:900;color:var(--black)}
.age-modal p{margin:6px auto 0;width:220px;font-size:10px;line-height:15px;color:var(--black)}
.age-actions{position:absolute;top:122px;left:41px;display:flex;gap:18px}
.age-actions span{width:84px;height:26px;border-radius:13px;line-height:26px;font-size:11px;font-weight:700;color:var(--white)}
.age-actions .exit{background:#2a2a2a}
.age-actions .enter{background:var(--green)}
</style>
</head>
<body>

<!-- Home page -->
<div class="screen screen--home">
  <div class="abs topbar">
    <div class="social"><span></span><span></span><span></span><span></span><span></span></div>
    <div class="call"><svg width="10" height="10" viewBox="0 0 10 10"><path d="M2 0.5 L3.6 2.6 L2.8 3.8 Q3.8 5.8 6 7.1 L7.2 6.3 L9.5 8 L8.4 9.5 Q3.5 9 0.5 1.8 Z" fill="#222"/></svg>Call Us Today : <b>1-800-555-0142</b></div>
  </div>
  <div class="abs navbar">
    <div class="brand">kestrelbrookhollow.com</div>
    <div class="menu"><span class="active">HOME</span><span>ABOUT US</span><span>SERVICES</span><span>TESTIMONIALS</span><span>BLOG</span><span>CONTACT US</span></div>
  </div>
  <div class="abs hero" role="img" aria-label="Hemp oil bottles, seeds and leaves on a wooden table">
    <h1>PAUSE, PLAY, REWIND</h1>
    <p>Nam convallis feugiat vulputatemaecenas tristique quis lorem eu fermentum.</p>
    <span class="btn btn--green">READ MORE</span>
    <div class="dots"><span></span><span></span><span></span><span></span></div>
  </div>
  <h2 class="title" style="top:535px">WELCOME TO OUR COMPANY NAME</h2>
  <p class="abs welcome-text">Lorem ipsum dolor sit amet, consectetur adipiscing elit. Donec sit amet fringilla turpis, sed semper nulla. Fusce feugiat, libero nec faucibus dictum, magna arcu consectetur turpis, ac eleifend metus ex eget elit. Sed sed dui pretium, volutpat lectus vel, tincidunt nulla.  Proin commodo id leo id vestibulum. Morbi et magna libero. Sed ut urna a nisi  venenatis gravida.</p>
  <span class="abs btn btn--orange" style="top:640px;left:326px">READ MORE</span>

  <div class="abs panel" style="top:705px;left:0;width:378px;height:277px;padding:66px 0 0 47px">
    <h3>HEMP</h3>
    <p>Lorem ipsum dolor sit amet, consectetur adipiscing elit. Donec sit amet fringilla turpis, sed semper nulla. Fusce feugiat, libero nec faucibus dictum, magna arcu consectetur turpis, ac eleifend metus ex eget elit. Sed sed dui pretium, volutpat lectus vel, tincidunt nulla.  Proin commodo id leo id vestibulum. Morbi et magna libero. Sed ut urna a nisi venenatis gravida</p>
    <span class="btn btn--orange">READ MORE</span>
  </div>
  <div class="photo" style="top:705px;left:378px;width:378px;height:277px;background:radial-gradient(circle at 55% 55%,#4e7a2a 0%,#5c4a3a 30%,#4a5a6a 65%,#2f3d4a 100%)" role="img" aria-label="Cupped hands holding soil with a young hemp seedling"></div>
  <div class="photo" style="top:982px;left:0;width:378px;height:293px;background:radial-gradient(circle at 50% 40%,#3fa535 0%,#1f6a1e 45%,#0e2d10 100%)" role="img" aria-label="Hemp leaf behind the CBD molecule diagram"></div>
  <div class="abs panel" style="top:982px;left:378px;width:378px;height:263px;padding:32px 0 0 26px">
    <h3>CBD</h3>
    <p>Lorem ipsum dolor sit amet, consectetur adipiscing elit. Donec sit amet fringilla turpis, sed semper nulla. Fusce feugiat, libero nec faucibus dictum, magna arcu consectetur turpis, ac eleifend metus ex eget elit. Sed sed dui pretium, volutpat lectus vel, tincidunt nulla.  Proin commodo id leo id vestibulum. Morbi et magna libero. Sed ut urna a nisi venenatis gravida</p>
    <span class="btn btn--orange">READ MORE</span>
  </div>
  <svg class="abs" style="top:700px;left:0" width="756" height="45" viewBox="0 0 756 45"><path d="M0 0 H756 V22 Q560 -4 378 30 Q180 48 0 38 Z" fill="#fff"/></svg>
  <svg class="abs" style="top:1235px;left:0" width="756" height="50" viewBox="0 0 756 50"><path d="M0 40 Q150 52 378 40 Q580 8 756 22 V50 H0 Z" fill="#fff"/></svg>

  <h2 class="title" style="top:1298px">BLOG POSTS</h2>
  <div class="blog" style="left:47px"><div class="thumb" style="background:linear-gradient(160deg,#b8a590,#7a5a3e 55%,#8d8a80)" role="img" aria-label="Bowl of hemp seeds with an oil bottle"></div><h4>NULLA RHONCUS PURUS SEM</h4><p>Lorem ipsum dolor sit amet, consectetur adipiscing elit. Donec sit amet fringilla turpis, sed semper nulla.</p><span class="btn btn--orange">READ MORE</span></div>
  <div class="blog" style="left:272px"><div class="thumb" style="background:radial-gradient(circle at 55% 60%,#6b5a2a,#2a1c12 55%,#120c08)" role="img" aria-label="Seedling sprouting from dark soil"></div><h4>NULLA RHONCUS PURUS SEM</h4><p>Lorem ipsum dolor sit amet, consectetur adipiscing elit. Donec sit amet fringilla turpis, sed semper nulla.</p><span class="btn btn--orange">READ MORE</span></div>
  <div class="blog" style="left:500px"><div class="thumb" style="background:linear-gradient(135deg,#2f7a2a,#c9b640 45%,#3a8a30 75%,#d8c870)" role="img" aria-label="CBD oil bottles among hemp leaves"></div><h4>NULLA RHONCUS PURUS SEM</h4><p>Lorem ipsum dolor sit amet, consectetur adipiscing elit. Donec sit amet fringilla turpis, sed semper nulla.</p><span class="btn btn--orange">READ MORE</span></div>

  <div class="abs reviews" style="top:1640px;left:0;width:756px;height:310px;background:var(--soft)">
    <div class="photo" style="top:20px;left:430px;width:280px;height:290px;background:linear-gradient(180deg,#ececec,#d6d6d6 50%,#2a2a2a 75%,#1c1c1c)" role="img" aria-label="Smiling man in gloves holding a CBD oil bottle"></div>
  </div>
  <svg class="abs" style="top:1636px;left:0" width="756" height="45" viewBox="0 0 756 45"><path d="M0 0 H756 V14 Q520 28 300 34 Q120 36 0 30 Z" fill="#fff"/></svg>
  <div class="reviews">
    <h3>CLIENT REVIEWS</h3>
    <div class="arrows">‹ ›</div>
    <div class="quote-mark">“</div>
    <p class="review-text">Lorem ipsum dolor sit amet, consectetur adipiscing elitonec sit amet fringilla turpis, sed semper nulla.  Fusce feugiat, libero nec faucibus dictum, magna arcu consec etur turpis, ac eleifend metus ex eget elit sed dui pretium,  volutpat lectus vel, tincidunt nulla. Proin commodo id leo id vestibulum morbi et magna  liberos ed ut urna a nisi ..”</p>
    <div class="reviewer">-NAME HEADING</div>
  </div>

  <div class="abs footer" role="img" aria-label="Darkened photo of hemp seeds">
    <svg class="abs" style="top:0;left:0" width="756" height="40" viewBox="0 0 756 40"><path d="M0 0 H756 V34 Q560 8 378 12 Q160 16 0 34 Z" fill="#f1f1f1"/></svg>
    <div class="fcol" style="left:47px"><h5>QUICK LINKS</h5><div class="pair"><span>Home</span><span>Testimonials</span><span>About Us</span><span>Blog</span><span>Services</span><span>Contact Us</span></div></div>
    <div class="fcol" style="left:225px"><h5>QUICK LINKS</h5>Nunc sagittis tempus<br>Blandit<br>Aenean elementum<br>Vivamus tempus</div>
    <div class="fcol" style="left:389px;line-height:18px"><h5 style="margin-bottom:4px">RESOURCES</h5>Nunc euismod<br>Accumsan tempor<br>Etiam ut lobortis<br>Ipsum nec risus sed</div>
    <div class="fcol" style="left:553px;line-height:16px"><h5 style="margin-bottom:6px">CONTACT INFO</h5>
      <div class="contact-row"><i>•</i><span>Etiam iaculis sollicitudin<br>pharetra ultricies</span></div>
      <div class="contact-row" style="margin-top:6px"><i>✆</i><span>1-800-555-0142</span></div>
      <div class="contact-row"><i>✉</i><span>info@kestrelbrookhollow.com</span></div>
    </div>
    <div class="fdivider"></div>
    <div class="copyright">Copyright © 2020 Company Name . All Right Reserved</div>
    <div class="social"><span></span><span></span><span></span><span></span><span></span></div>
  </div>
</div>

<!-- Home page with age gate -->
<div class="screen screen--gate">
  <div class="abs topbar">
    <div class="social"><span></span><span></span><span></span><span></span><span></span></div>
    <div class="call"><svg width="10" height="10" viewBox="0 0 10 10"><path d="M2 0.5 L3.6 2.6 L2.8 3.8 Q3.8 5.8 6 7.1 L7.2 6.3 L9.5 8 L8.4 9.5 Q3.5 9 0.5 1.8 Z" fill="#222"/></svg>Call Us Today : <b>1-800-555-0142</b></div>
  </div>
  <div class="abs navbar">
    <div class="brand">kestrelbrookhollow.com</div>
    <div class="menu"><span class="active">HOME</span><span>ABOUT US</span><span>SERVICES</span><span>TESTIMONIALS</span><span>BLOG</span><span>CONTACT US</span></div>
  </div>
  <div class="abs hero" role="img" aria-label="Hemp oil bottles, seeds and leaves on a wooden table">
    <h1>PAUSE, PLAY, REWIND</h1>
    <p>Nam convallis feugiat vulputatemaecenas tristique quis lorem eu fermentum.</p>
    <span class="btn btn--green">READ MORE</span>
    <div class="dots"><span></span><span></span><span></span><span></span></div>
  </div>
  <h2 class="title" style="top:535px">WELCOME TO OUR COMPANY NAME</h2>
  <p class="abs welcome-text">Lorem ipsum dolor sit amet, consectetur adipiscing elit. Donec sit amet fringilla turpis, sed semper nulla. Fusce feugiat, libero nec faucibus dictum, magna arcu consectetur turpis, ac eleifend metus ex eget elit. Sed sed dui pretium, volutpat lectus vel, tincidunt nulla.  Proin commodo id leo id vestibulum. Morbi et magna libero. Sed ut urna a nisi  venenatis gravida.</p>
  <span class="abs btn btn--orange" style="top:640px;left:326px">READ MORE</span>

  <div class="abs panel" style="top:705px;left:0;width:378px;height:277px;padding:66px 0 0 47px">
    <h3>HEMP</h3>
    <p>Lorem ipsum dolor sit amet, consectetur adipiscing elit. Donec sit amet fringilla turpis, sed semper nulla. Fusce feugiat, libero nec faucibus dictum, magna arcu consectetur turpis, ac eleifend metus ex eget elit. Sed sed dui pretium, volutpat lectus vel, tincidunt nulla.  Proin commodo id leo id vestibulum. Morbi et magna libero. Sed ut urna a nisi venenatis gravida</p>
    <span class="btn btn--orange">READ MORE</span>
  </div>
  <div class="photo" style="top:705px;left:378px;width:378px;height:277px;background:radial-gradient(circle at 55% 55%,#4e7a2a 0%,#5c4a3a 30%,#4a5a6a 65%,#2f3d4a 100%)" role="img" aria-label="Cupped hands holding soil with a young hemp seedling"></div>
  <div class="photo" style="top:982px;left:0;width:378px;height:293px;background:radial-gradient(circle at 50% 40%,#3fa535 0%,#1f6a1e 45%,#0e2d10 100%)" role="img" aria-label="Hemp leaf behind the CBD molecule diagram"></div>
  <div class="abs panel" style="top:982px;left:378px;width:378px;height:263px;padding:32px 0 0 26px">
    <h3>CBD</h3>
    <p>Lorem ipsum dolor sit amet, consectetur adipiscing elit. Donec sit amet fringilla turpis, sed semper nulla. Fusce feugiat, libero nec faucibus dictum, magna arcu consectetur turpis, ac eleifend metus ex eget elit. Sed sed dui pretium, volutpat lectus vel, tincidunt nulla.  Proin commodo id leo id vestibulum. Morbi et magna libero. Sed ut urna a nisi venenatis gravida</p>
    <span class="btn btn--orange">READ MORE</span>
  </div>
  <svg class="abs" style="top:700px;left:0" width="756" height="45" viewBox="0 0 756 45"><path d="M0 0 H756 V22 Q560 -4 378 30 Q180 48 0 38 Z" fill="#fff"/></svg>
  <svg class="abs" style="top:1235px;left:0" width="756" height="50" viewBox="0 0 756 50"><path d="M0 40 Q150 52 378 40 Q580 8 756 22 V50 H0 Z" fill="#fff"/></svg>

  <h2 class="title" style="top:1298px">BLOG POSTS</h2>
  <div class="blog" style="left:47px"><div class="thumb" style="background:linear-gradient(160deg,#b8a590,#7a5a3e 55%,#8d8a80)" role="img" aria-label="Bowl of hemp seeds with an oil bottle"></div><h4>NULLA RHONCUS PURUS SEM</h4><p>Lorem ipsum dolor sit amet, consectetur adipiscing elit. Donec sit amet fringilla turpis, sed semper nulla.</p><span class="btn btn--orange">READ MORE</span></div>
  <div class="blog" style="left:272px"><div class="thumb" style="background:radial-gradient(circle at 55% 60%,#6b5a2a,#2a1c12 55%,#120c08)" role="img" aria-label="Seedling sprouting from dark soil"></div><h4>NULLA RHONCUS PURUS SEM</h4><p>Lorem ipsum dolor sit amet, consectetur adipiscing elit. Donec sit amet fringilla turpis, sed semper nulla.</p><span class="btn btn--orange">READ MORE</span></div>
  <div class="blog" style="left:500px"><div class="thumb" style="background:linear-gradient(135deg,#2f7a2a,#c9b640 45%,#3a8a30 75%,#d8c870)" role="img" aria-label="CBD oil bottles among hemp leaves"></div><h4>NULLA RHONCUS PURUS SEM</h4><p>Lorem ipsum dolor sit amet, consectetur adipiscing elit. Donec sit amet fringilla turpis, sed semper nulla.</p><span class="btn btn--orange">READ MORE</span></div>

  <div class="abs reviews" style="top:1640px;left:0;width:756px;height:310px;background:var(--soft)">
    <div class="photo" style="top:20px;left:430px;width:280px;height:290px;background:linear-gradient(180deg,#ececec,#d6d6d6 50%,#2a2a2a 75%,#1c1c1c)" role="img" aria-label="Smiling man in gloves holding a CBD oil bottle"></div>
  </div>
  <svg class="abs" style="top:1636px;left:0" width="756" height="45" viewBox="0 0 756 45"><path d="M0 0 H756 V14 Q520 28 300 34 Q120 36 0 30 Z" fill="#fff"/></svg>
  <div class="reviews">
    <h3>CLIENT REVIEWS</h3>
    <div class="arrows">‹ ›</div>
    <div class="quote-mark">“</div>
    <p class="review-text">Lorem ipsum dolor sit amet, consectetur adipiscing elitonec sit amet fringilla turpis, sed semper nulla.  Fusce feugiat, libero nec faucibus dictum, magna arcu consec etur turpis, ac eleifend metus ex eget elit sed dui pretium,  volutpat lectus vel, tincidunt nulla. Proin commodo id leo id vestibulum morbi et magna  liberos ed ut urna a nisi ..”</p>
    <div class="reviewer">-NAME HEADING</div>
  </div>

  <div class="abs footer" role="img" aria-label="Darkened photo of hemp seeds">
    <svg class="abs" style="top:0;left:0" width="756" height="40" viewBox="0 0 756 40"><path d="M0 0 H756 V34 Q560 8 378 12 Q160 16 0 34 Z" fill="#f1f1f1"/></svg>
    <div class="fcol" style="left:47px"><h5>QUICK LINKS</h5><div class="pair"><span>Home</span><span>Testimonials</span><span>About Us</span><span>Blog</span><span>Services</span><span>Contact Us</span></div></div>
    <div class="fcol" style="left:225px"><h5>QUICK LINKS</h5>Nunc sagittis tempus<br>Blandit<br>Aenean elementum<br>Vivamus tempus</div>
    <div class="fcol" style="left:389px;line-height:18px"><h5 style="margin-bottom:4px">RESOURCES</h5>Nunc euismod<br>Accumsan tempor<br>Etiam ut lobortis<br>Ipsum nec risus sed</div>
    <div class="fcol" style="left:553px;line-height:16px"><h5 style="margin-bottom:6px">CONTACT INFO</h5>
      <div class="contact-row"><i>•</i><span>Etiam iaculis sollicitudin<br>pharetra ultricies</span></div>
      <div class="contact-row" style="margin-top:6px"><i>✆</i><span>1-800-555-0142</span></div>
      <div class="contact-row"><i>✉</i><span>info@kestrelbrookhollow.com</span></div>
    </div>
    <div class="fdivider"></div>
    <div class="copyright">Copyright © 2020 Company Name . All Right Reserved</div>
    <div class="social"><span></span><span></span><span></span><span></span><span></span></div>
  </div>

  <div class="overlay"></div>
  <div class="age-modal" role="dialog" aria-label="Age verification">
    <span class="close">x</span>
    <h3>AGE VERIFICATION</h3>
    <p>Aenean nisi nisi, luctus nec urna ac, maximus imperdiet libero</p>
    <div class="age-actions"><span class="exit">Exist</span><span class="enter">Im Over 20</span></div>
  </div>
</div>

</body>
</html>
```